Lumra Learning Web Design Project

Who We are:
Lumra Learning is education information portal/ magazine, providing information about the Chinese and International education markets. Our aim is to help school principals improve there curriculum, and parents in understanding this curriculum.

Project Brief:
The site will include education news updates, educational services, curriculum developments and overseas study. We hope the site represents the cross cultural bridge between the west and east. The site will cover both the Sciences and Arts.

Note:
The logo design competition is also underway so we only need the website design

What We want:
This competition is for Design only no coding!
Design a home page based on Template 1,2 or 3. I only need to select one.
The design of an article page.

Optional
Design a Parvex Shutters metro style splash page.

Sites We like:
http://www.qv.com.cn/tonguebridge/default.aspx
http://www.dailyuniversitybulletin.co.uk/
http://kptz.sinocraftlearn.net/

Template Explanations:
Template 1-
The main information has a dynamic sliding category view that when clicked displays the relevant info.
In addition to the main upper menu it also has a left hand sliding menu that pops out on click or gesture

Template 2-
Has limited number of Articles most of the menus are drop downs from the top menu

Template 3-
No Top menu

Target Market(s)

Teachers, principals and parents

Industry/Entity Type

Education

Requirements
Should not have
• kindergarten preschool feel

```html
<!DOCTYPE html>
<html lang="en">
<head>
<meta charset="utf-8">
<title>Lumra Learning</title>
<link rel="stylesheet" href="https://fonts.googleapis.com/css2?family=Ubuntu:wght@300;400;500&family=Roboto+Condensed:wght@700&display=swap">
<style>
:root{
  --bg:#e6e8eb;
  --page:#ffffff;
  --brand:#1d4a8c;
  --red:#d92a2a;
  --red-dark:#c01818;
  --blue:#1f5a96;
  --blue-dark:#164477;
  --link:#1f5aa6;
  --text:#333;
  --muted:#8a8a8a;
  --line:#e3e3e3;
  --nav-home:#7b2bd1;
  --nav-about:#c41a1a;
  --nav-services:#f25a14;
  --nav-blog:#f7a02a;
  --nav-news:#f5c400;
  --nav-career:#8cc63f;
  --nav-articles:#29c3d9;
  --nav-support:#0d2d6b;
  --nav-contact:#ee1d8a;
  --footer-dark:#2f3033;
}
*{box-sizing:border-box;margin:0;padding:0}
html,body{width:918px;height:1200px;overflow:hidden}
body{background:radial-gradient(circle at 30% 30%,#f1f2f4,var(--bg));font-family:"Ubuntu",sans-serif;color:var(--text);position:relative}
.page{position:absolute;left:78px;top:0;width:759px;height:1200px;background:var(--page)}
.abs{position:absolute}
ul{list-style:none}

.logo{left:106px;top:28px;display:flex;flex-direction:column;align-items:center;width:140px}
.logo-mark{width:40px;height:40px;border-radius:50%;background:var(--red)}
.logo-name{margin-top:10px;font-size:15px;font-weight:500;color:var(--brand);letter-spacing:.3px;white-space:nowrap}

.search{left:629px;top:74px;width:192px;height:24px;border:1px solid #d6d6d6;border-radius:3px;font-size:9px;font-style:italic;color:#999;padding:6px 10px;font-weight:300}
.search svg{position:absolute;right:6px;top:4px}

.nav{left:90px;top:112px;height:40px;display:flex;width:736px;border-radius:3px;overflow:hidden}
.nav a{display:flex;align-items:center;justify-content:center;color:#fff;font-family:"Roboto Condensed",sans-serif;font-weight:700;font-size:12.5px;text-decoration:none;box-shadow:inset 0 -6px 8px rgba(0,0,0,.08)}

.hero{left:91px;top:159px;width:735px;height:236px;border-radius:4px;background:linear-gradient(90deg,#9a7b63,#d9c6b5 30%,#c3a58d 55%,#7f8a5a 80%,#6f5a44)}
.dots{left:437px;top:380px;display:flex;gap:3px}
.dots i{width:9px;height:9px;border-radius:50%;background:#fff;display:block}

.box{border:1px solid var(--line);background:#fff}
.head{height:33px;color:#fff;font-size:14.5px;padding:8px 21px;font-weight:400}
.head.red{background:linear-gradient(#e63b3b,var(--red-dark))}
.head.blue{background:linear-gradient(var(--blue),var(--blue-dark))}
.head.grey{background:linear-gradient(#fafafa,#ececec);color:#333}

.menu li{height:23px;border-bottom:1px solid var(--line);font-size:9px;color:#555;padding:6px 0 0 30px;position:relative}
.menu li::before{content:"";position:absolute;left:20px;top:9px;border:3px solid transparent;border-left:3px solid #999;border-right:0}

.connect-title{font-size:10px;margin:14px 0 0 14px;color:#333}
.connect-text{font-size:8px;color:var(--muted);margin:5px 14px 0;line-height:13px}
.social{display:flex;gap:4px;margin:10px 0 0 14px}
.social i{width:22px;height:22px;border-radius:4px;background:linear-gradient(#4aa0e0,#1d6fb8);display:block}

.cats{left:261px;top:410px;width:374px;height:256px}
.cat-col{position:absolute;top:50px}
.cat-col li{font-size:9px;color:var(--link);height:21.6px;padding-left:10px;position:relative}
.cat-col li::before{content:"";position:absolute;left:0;top:3px;border:3px solid transparent;border-left:3px solid var(--brand);border-right:0}
.regions{position:absolute;left:0;top:171px;width:374px}
.regions div{height:28px;border-top:1px solid #fff;background:linear-gradient(#eef3f8,#d9e5f0);position:relative;font-size:10.5px;color:var(--brand)}
.regions span{position:absolute;top:8px}

.article-img{height:74px;border:4px solid #fff;box-shadow:0 0 2px rgba(0,0,0,.3);background:linear-gradient(135deg,#8c9aa8,#d4c2a8 50%,#6b7d5e)}
.article-title{font-size:10px;color:#333}
.article-text{font-size:8px;color:var(--muted);line-height:13.6px;width:160px}
.thumb{top:874px;width:76px;height:57px;border:4px solid #fff;box-shadow:0 0 2px rgba(0,0,0,.3);background:linear-gradient(135deg,#5f7f9e,#c9b9a0)}

.news-title{font-size:10px;color:var(--link)}
.news-text{font-size:8px;color:var(--muted);line-height:13.6px;margin-top:4px;width:150px}
.popular li{height:23px;border-bottom:1px solid var(--line);font-size:9px;color:var(--red);padding:6px 0 0 15px;position:relative;margin:0 14px 0 20px}
.popular li::before{content:"";position:absolute;left:2px;top:9px;border:3.5px solid transparent;border-left:3.5px solid var(--red);border-right:0}

.footer{left:87px;top:968px;width:739px;height:181px;border:1px solid var(--line);border-bottom:0;background:linear-gradient(#fff,#eeeeee);border-radius:4px 4px 0 0}
.fcol{position:absolute;top:26px}
.fcol h3{font-size:13.5px;font-weight:400;color:#333;margin-bottom:6px}
.fcol li{font-size:8px;color:#666;height:17.4px}
.fdiv{position:absolute;top:28px;width:1px;height:102px;background:#ddd}
.bar{left:87px;top:1149px;width:739px;height:33px;background:var(--footer-dark);color:#bbb;font-size:8px;padding:12px 38px;font-weight:300}
</style>
</head>
<body>
<div class="page"></div>

<div class="abs logo"><span class="logo-mark"></span><span class="logo-name">LUMRA LEARNING</span></div>

<div class="abs search">Search here..
  <svg width="14" height="14" viewBox="0 0 14 14"><circle cx="6" cy="6" r="4.5" fill="none" stroke="#888" stroke-width="1.4"/><line x1="9.3" y1="9.3" x2="13" y2="13" stroke="#888" stroke-width="1.6"/></svg>
</div>

<nav class="abs nav">
  <a style="width:74px;background:var(--nav-home)">HOME</a>
  <a style="width:86px;background:var(--nav-about)">ABOUT US</a>
  <a style="width:87px;background:var(--nav-services)">SERVICES</a>
  <a style="width:92px;background:var(--nav-blog)">BLOG POST</a>
  <a style="width:68px;background:var(--nav-news)">NEWS</a>
  <a style="width:78px;background:var(--nav-career)">CAREER</a>
  <a style="width:84px;background:var(--nav-articles)">ARTICLES</a>
  <a style="width:83px;background:var(--nav-support)">SUPPORT</a>
  <a style="width:84px;background:var(--nav-contact)">CONTACT</a>
</nav>

<div class="abs hero" role="img" aria-label="Photo of four smiling students holding notebooks in front of a campus building"></div>
<div class="abs dots"><i></i><i></i><i></i><i></i></div>

<!-- Left column -->
<div class="abs box" style="left:88px;top:408px;width:162px;height:367px;border-top:0">
  <div class="head red">Select Menu</div>
  <ul class="menu" style="margin-top:4px">
    <li>Maecenas aliquet</li><li>Mauris malesuada</li><li>Ultricies amet</li><li>Porttitor mattis enim</li><li>Libero interdum</li><li>Blandit sed</li><li>Tempor cursus</li><li>Maecenas aliquet</li><li>Mauris malesuada</li><li>Ultricies amet</li><li>Porttitor mattis enim</li><li>Libero interdum</li><li>Blandit sed</li><li style="border:0">Tempor cursus</li>
  </ul>
</div>
<div class="abs box" style="left:88px;top:785px;width:162px;height:165px;border-top:0">
  <div class="head blue" style="height:31px;padding-top:7px">Get Connected</div>
  <p class="connect-title">Get in touch with us</p>
  <p class="connect-text">Sociosqu ad litora torquent per conubia nostra, per inceptos</p>
  <div class="social"><i></i><i></i><i></i><i></i></div>
</div>

<!-- Middle column -->
<div class="abs box cats" style="border-top:0">
  <div class="head blue" style="height:33px">Categories</div>
  <ul class="cat-col" style="left:25px"><li>Maecenas aliquet</li><li>Mauris malesuada</li><li>Ultricies amet</li><li>Porttitor mattis enim</li><li>Libero interdum</li></ul>
  <ul class="cat-col" style="left:148px"><li>Blandit sed</li><li>Tempor cursus</li><li>Maecenas aliquet</li><li>Mauris malesuada</li><li>Ultricies amet</li></ul>
  <ul class="cat-col" style="left:257px"><li>Porttitor mattis enim</li><li>Libero interdum</li><li>Blandit sed</li><li>Tempor cursus</li></ul>
  <div class="regions">
    <div><span style="left:23px">EUROPE</span><span style="left:128px">DRAMA</span><span style="left:257px">MATH</span></div>
    <div><span style="left:23px">ASIA</span><span style="left:128px">SCIENCE</span><span style="left:257px">BUSINESS STUDIES</span></div>
    <div><span style="left:23px">USA</span><span style="left:128px">ENGLISH</span><span style="left:257px">E COMMERCE</span></div>
  </div>
</div>

<div class="abs box" style="left:261px;top:675px;width:374px;height:275px">
  <div class="head grey" style="height:34px;padding:10px 16px">Latest Articles</div>
</div>
<div class="abs article-img" style="left:276px;top:722px;width:162px" role="img" aria-label="Photo of students chatting on campus stairs"></div>
<div class="abs article-img" style="left:452px;top:722px;width:166px" role="img" aria-label="Photo of a teacher with students at computers"></div>
<p class="abs article-title" style="left:278px;top:803px">Class aptent taciti</p>
<p class="abs article-text" style="left:278px;top:819px">Sociosqu ad litora torquent per conubia nostra, per inceptos hymenaeos. Proin nulla arcu, nonummy luctus</p>
<p class="abs article-title" style="left:452px;top:803px">Curabitur metus ipsum</p>
<p class="abs article-text" style="left:452px;top:819px">Sociosqu ad litora torquent per conubia nostra, per inceptos hymenaeos. Proin nulla arcu, nonummy luctus</p>
<div class="abs thumb" style="left:276px" role="img" aria-label="Photo of two students studying"></div>
<div class="abs thumb" style="left:364px" role="img" aria-label="Photo of a globe and books"></div>
<div class="abs thumb" style="left:454px" role="img" aria-label="Photo of a student writing"></div>
<div class="abs thumb" style="left:542px" role="img" aria-label="Photo of students in a classroom"></div>

<!-- Right column -->
<div class="abs box" style="left:645px;top:410px;width:181px;height:300px">
  <div class="head grey" style="height:34px;padding:10px 16px">Latest News</div>
</div>
<div class="abs" style="left:662px;top:456px">
  <p class="news-title">Duis tincidunt lectus</p>
  <p class="news-text">Suspendisse vulputate aliquam dui. Nulla elementum dui ut augue.</p>
</div>
<div class="abs" style="left:662px;top:517px">
  <p class="news-title">Scelerisque mi tortor at ipsum</p>
  <p class="news-text">Ut ac mi quis lacus mollis aliquam. Curabitur iaculis tempus</p>
</div>
<div class="abs" style="left:662px;top:578px">
  <p class="news-title">Phasellus felis dolor</p>
  <p class="news-text">Ut ac mi quis lacus mollis aliquam. Curabitur iaculis tempus eros.</p>
</div>
<div class="abs" style="left:665px;top:639px">
  <p class="news-title">Duis tincidunt lectus</p>
  <p class="news-text">Class aptent taciti sociosqu ad litora torquent per conubia nostra, per inceptos hymenaeos.</p>
</div>

<div class="abs box" style="left:645px;top:722px;width:181px;height:226px;border-top:0">
  <div class="head red" style="height:34px;padding:9px 19px">Most Popular</div>
  <ul class="popular" style="margin-top:13px">
    <li>Maecenas aliquet velit vel</li><li>Mauris neque malesuada</li><li>Nec ultricies sit amet</li><li>Porttitor mattis enim</li><li>In massa libero interdum</li><li>Blandit sed nulla</li><li style="border:0">Est eget tempor cursus</li>
  </ul>
</div>

<!-- Footer -->
<footer class="abs footer">
  <div class="fcol" style="left:40px"><h3>About Us</h3><ul><li>Overview</li><li>About Us</li><li>What We Do</li><li>How we teach</li><li>Blog Post</li></ul></div>
  <div class="fdiv" style="left:124px"></div>
  <div class="fcol" style="left:155px"><h3>Services Provide</h3><ul><li>Mauris neque metus</li><li>Malesuada nec</li><li>Ultricies sit amet</li><li>Porttitor mattis</li><li>Massa libero</li></ul></div>
  <div class="fdiv" style="left:274px"></div>
  <div class="fcol" style="left:298px"><h3>Sublinks</h3><ul><li>Mauris neque metus</li><li>Malesuada nec</li><li>Ultricies sit amet</li><li>Porttitor mattis</li><li>Massa libero</li></ul></div>
  <div class="fdiv" style="left:404px"></div>
  <div class="fcol" style="left:431px"><h3>Sublinks</h3><ul><li>Mauris neque metus</li><li>Malesuada nec</li><li>Ultricies sit amet</li><li>Porttitor mattis</li><li>Massa libero</li></ul></div>
  <div class="fdiv" style="left:533px"></div>
  <div class="fcol" style="left:561px"><h3>Sublinks</h3><ul><li>Mauris neque metus</li><li>Malesuada nec</li><li>Ultricies sit amet</li><li>Porttitor mattis</li><li>Massa libero</li></ul></div>
</footer>
<div class="abs bar">Copyright © 2013 Company Name.&nbsp; All right reserved.</div>
</body>
</html>
```